The Marigold Venture WEBSITE DESIGN

Marigold is a not for profit working in international aid and development. The website needs to be lively not depressing,earthy rather than bling, have a dramatic impact over lightweight. It may be that a black and white with spot colour may be more impacting given the simplicity I want for the site. Marigold works in partnership with registered NGOs in Asia and Africa. At any one time it will have about five feature projects. The purpose is for people to be able to find out about the projects, the countries, the partner organisations, people's stories and then give people the opportunity to give their financial and volunteer support.

Target Market(s)

First World Donors
All ages but particularly 25 - 55

Industry/Entity Type

Human Rights

Number of Pages Required

5+ page

Font styles to use
Sans Serif

Requirements
Must have
• Simplicity
• Easy access to giving options
• Highlight stories both video and image + copy (sample in attachments)
• Lots of images over copy
Nice to have
• Interest
• Not boring
• May work in black and white with a spot colour or sepia look
Should not have
• Shiny new look
• Dont know how many pages or if it be coded or uncoded - makes no sense to me

```html
<!DOCTYPE html>
<html lang="en">
<head>
<meta charset="utf-8">
<title>The Marigold Venture</title>
<link rel="stylesheet" href="https://fonts.googleapis.com/css2?family=Open+Sans:wght@400;600;700&family=Lora:wght@400&display=swap">
<style>
:root{
  --orange:#f39a1e;
  --blue:#3b9fd9;
  --teal:rgba(88,190,178,.88);
  --ink:#3d3d3d;
  --muted:#8a8a8a;
  --rule:#e3e3e3;
  --paper:#ffffff;
  --footer:#ececec;
  --photo-warm:#b98a5a;
  --photo-green:#6f8a4a;
}
*{box-sizing:border-box;margin:0;padding:0}
html,body{width:717px;height:1200px;overflow:hidden;background:var(--paper)}
body{font-family:"Open Sans",Arial,sans-serif;color:var(--ink);position:relative}
.site-header{height:72px;display:flex;align-items:center;justify-content:center;gap:10px}
.brand-dot{width:22px;height:22px;border-radius:50%;background:var(--orange)}
.brand-name{font-size:22px;font-weight:700;color:var(--orange);letter-spacing:.5px}
.main-nav{height:18px;background:var(--orange);display:flex;justify-content:center;gap:26px;align-items:center}
.main-nav a{color:#fff;font-size:8px;font-weight:600;text-decoration:none}
.hero{position:relative;height:294px;background:linear-gradient(120deg,var(--photo-green) 0%,var(--photo-warm) 45%,#8a5f3c 75%,#5f7a3c 100%)}
.hero-caption{position:absolute;left:84px;top:110px;width:290px;padding:14px 18px;background:var(--teal);color:#fff}
.hero-caption h1{font-family:"Lora",Georgia,serif;font-weight:400;font-size:25px;line-height:1.05}
.hero-caption h1 span{display:block;font-size:20px}
.hero-caption p{font-size:7px;line-height:1.4;margin-top:6px}
.slider-dots{position:absolute;bottom:10px;left:50%;transform:translateX(-50%);display:flex;gap:5px}
.slider-dots i{width:7px;height:7px;border-radius:50%;background:rgba(255,255,255,.6)}
.slider-dots i:first-child{background:#fff}
.about{padding:20px 110px 0;text-align:center}
.section-title{font-size:19px;font-weight:400;color:var(--ink)}
.about-lead{font-size:8px;line-height:1.5;margin-top:8px;color:var(--ink)}
.about-body{font-size:6.5px;line-height:1.55;margin-top:8px;color:var(--muted)}
.pillars{display:flex;gap:22px;padding:16px 110px 0}
.pillar{flex:1;border-top:1px solid var(--rule);padding-top:8px}
.pillar h3{font-size:10px;font-weight:600;color:var(--orange)}
.pillar p{font-size:6.5px;line-height:1.55;color:var(--muted);margin-top:4px}
.projects{position:absolute;top:620px;left:0;width:717px;height:190px;background:var(--blue);color:#fff;text-align:center}
.projects .section-title{color:#fff;margin-top:18px}
.project-list{display:flex;justify-content:center;gap:46px;margin-top:16px}
.project{width:120px}
.project-map{width:62px;height:48px;margin:0 auto;border-radius:40% 55% 45% 50%;background:rgba(255,255,255,.8)}
.project h3{font-size:10px;font-weight:600;margin-top:8px}
.project p{font-size:6.5px;line-height:1.45;margin-top:3px;opacity:.9}
.stories{position:absolute;top:830px;left:110px;width:497px}
.stories .section-title{font-size:15px;text-align:left}
.stories-grid{display:flex;gap:16px;margin-top:10px}
.story-list{width:235px}
.story{display:flex;gap:8px;margin-bottom:12px}
.story-thumb{width:62px;height:50px;flex:none;background:linear-gradient(135deg,var(--photo-warm),var(--photo-green))}
.story h4{font-size:8px;font-weight:600;color:var(--orange)}
.story p{font-size:6.5px;line-height:1.5;color:var(--muted);margin-top:2px}
.story a{font-size:6.5px;color:var(--blue);text-decoration:none}
.video-grid{flex:1;display:grid;grid-template-columns:1fr 1fr;gap:6px}
.video{position:relative}
.video-thumb{height:46px;background:linear-gradient(135deg,#6b4b34,var(--photo-warm))}
.video-thumb svg{position:absolute;left:50%;top:23px;transform:translate(-50%,-50%)}
.video p{font-size:6px;line-height:1.4;color:var(--muted);margin-top:3px}
.giving-band{position:absolute;top:1010px;left:0;width:717px;height:150px;background:var(--orange);color:#fff;display:flex;padding:0 110px;align-items:center;gap:16px}
.giving-photo{width:78px;height:78px;border-radius:50%;border:3px solid #fff;background:linear-gradient(135deg,#7a5236,var(--photo-warm));flex:none}
.giving-text{width:190px}
.giving-band h2{font-size:15px;font-weight:600;letter-spacing:.5px}
.giving-band p{font-size:6.5px;line-height:1.5;margin-top:3px}
.follow{margin-left:auto;width:190px}
.social{display:flex;gap:5px;margin-top:6px}
.social i{width:11px;height:11px;border-radius:50%;background:#fff;display:block}
.site-footer{position:absolute;top:1160px;left:0;width:717px;height:40px;background:var(--footer);padding:9px 110px;font-size:7px;color:var(--muted)}
.footer-nav{display:flex;gap:8px}
.footer-nav a{color:var(--ink);text-decoration:none}
.footer-social{position:absolute;right:110px;top:9px;display:flex;gap:5px}
.footer-social i{width:9px;height:9px;border-radius:50%;background:#9a9a9a;display:block}
.copyright{margin-top:5px;font-size:6px}
</style>
</head>
<body>
<header class="site-header">
  <span class="brand-dot"></span>
  <span class="brand-name">The Marigold Venture</span>
</header>
<nav class="main-nav">
  <a href="#">About Project</a><a href="#">Introduction to 3 Current Projects</a><a href="#">News/Stories</a><a href="#">Giving</a><a href="#">Contact</a>
</nav>
<section class="hero" role="img" aria-label="Photo of smiling women and children in a village">
  <div class="hero-caption">
    <h1>Protects and shades<span>other plants in the garden</span></h1>
    <p>A small act of care can let a whole community grow strong and bloom together.</p>
  </div>
  <div class="slider-dots"><i></i><i></i><i></i></div>
</section>
<section class="about">
  <h2 class="section-title">About Marigold</h2>
  <p class="about-lead">As a not-for-profit Marigold partners with registered NGOs across Asia and Africa, supporting local people to build lasting change in their own communities.</p>
  <p class="about-body">We believe aid should be lively, hopeful and rooted in partnership. Each project is chosen with care, guided by the people it serves, and shared openly with every donor who makes it possible. Together we plant seeds that grow long after our support ends.</p>
</section>
<div class="pillars">
  <div class="pillar"><h3>Purpose</h3><p>To walk alongside local partners, funding practical projects in health, education and livelihoods so families can shape their own future.</p></div>
  <div class="pillar"><h3>Values</h3><p>Respect, honesty and shared learning guide everything we do, from the first conversation with a partner to reporting back to donors.</p></div>
  <div class="pillar"><h3>Meaning of name</h3><p>The marigold grows easily, brightens the ground around it and protects other plants, a picture of quiet, steady support.</p></div>
</div>
<section class="projects">
  <h2 class="section-title">Introduction to 3 Current Projects</h2>
  <div class="project-list">
    <div class="project"><div class="project-map" role="img" aria-label="Map outline of the project country"></div><h3>Riverbend Partners</h3><p>Helping rural families reach clean water, schooling and fair work.</p></div>
    <div class="project"><div class="project-map" role="img" aria-label="Map outline of the project country"></div><h3>Green Hills Circle</h3><p>Supporting women's savings groups and small farms in the hills.</p></div>
    <div class="project"><div class="project-map" role="img" aria-label="Map outline of the project country"></div><h3>Open Door Youth</h3><p>Training young people in trades and building local clinics together.</p></div>
  </div>
</section>
<section class="stories">
  <h2 class="section-title">News/Stories from Projects</h2>
  <div class="stories-grid">
    <div class="story-list">
      <article class="story"><div class="story-thumb" role="img" aria-label="Photo of a village shop"></div><div><h4>Rosalind's Story</h4><p>Rosalind shares how a small loan became a thriving village shop supporting her three children.</p><a href="#">read more</a></div></article>
      <article class="story"><div class="story-thumb" role="img" aria-label="Photo of farmers in a field"></div><div><h4>Amani's Story</h4><p>After joining a savings group, Amani trained neighbours in farming and now leads the cooperative.</p><a href="#">read more</a></div></article>
    </div>
    <div class="video-grid">
      <div class="video"><div class="video-thumb" role="img" aria-label="Video still of a classroom"><svg width="14" height="14" viewBox="0 0 14 14"><circle cx="7" cy="7" r="7" fill="#fff" opacity=".85"/><path d="M5.5 4v6l5-3z" fill="#555"/></svg></div></div>
      <div class="video"><div class="video-thumb" role="img" aria-label="Video still of a community meeting"><svg width="14" height="14" viewBox="0 0 14 14"><circle cx="7" cy="7" r="7" fill="#fff" opacity=".85"/><path d="M5.5 4v6l5-3z" fill="#555"/></svg></div></div>
      <div class="video"><div class="video-thumb" role="img" aria-label="Video still of a village school"><svg width="14" height="14" viewBox="0 0 14 14"><circle cx="7" cy="7" r="7" fill="#fff" opacity=".85"/><path d="M5.5 4v6l5-3z" fill="#555"/></svg></div><p>A day at the village school</p></div>
      <div class="video"><div class="video-thumb" role="img" aria-label="Video still of a women's group"><svg width="14" height="14" viewBox="0 0 14 14"><circle cx="7" cy="7" r="7" fill="#fff" opacity=".85"/><path d="M5.5 4v6l5-3z" fill="#555"/></svg></div><p>Women's savings group meets weekly</p></div>
    </div>
  </div>
</section>
<section class="giving-band">
  <div class="giving-photo" role="img" aria-label="Portrait photo of a child"></div>
  <div class="giving-text"><h2>GIVING</h2><p>Your gift, large or small, helps our partners bring lasting change. Give once, give monthly or volunteer your time.</p></div>
  <div class="follow"><h2>FOLLOW US</h2><p>Stay close to the stories from our projects and share them with friends.</p><div class="social"><i></i><i></i><i></i></div></div>
</section>
<footer class="site-footer">
  <nav class="footer-nav"><a href="#">About Marigold</a>|<a href="#">Introduction to 3 Current Projects</a>|<a href="#">News/Stories</a>|<a href="#">Giving</a>|<a href="#">Contact</a></nav>
  <div class="footer-social"><i></i><i></i><i></i><i></i></div>
  <p class="copyright">© 2024 The Marigold Venture. All rights reserved.</p>
</footer>
</body>
</html>
```